IT Company needs full suite of stationery

Our company 4627 Vantor Holdings Inc. is an IT company based in Toronto, Canada. Based on our logo we would like to see business cards(front and back), letterhead, envelope, brochure template. Design would be simple, not too bright, modern but can be used for many years, good theme throughout. Our official logo is the the fullcolor_a, full company name is 4627 Vantor Holdings Inc., Please include full company name on all pieces. Logo can be modified to be the graphic only with the "4627 Holdings", I have cropped it myself for a couple files but I am no designer. We will provide lots of feedback so post early and often.

Project Deadline Extended
Reason: Very busy around the holidays, like a lot of the designs currently submitted, will definitely be picking one. Thanks for your submissions and merry Christmas and Happy New Year to everyone.

Industry/Entity Type

Business

```html
<!DOCTYPE html>
<html lang="en">
<head>
<meta charset="utf-8">
<title>4627 Vantor Holdings Inc. – Stationery Suite</title>
<link href="https://fonts.googleapis.com/css2?family=Montserrat:wght@600&family=Arimo:wght@400;700&display=swap" rel="stylesheet">
<style>
:root{
  --green:#5aa83a;
  --green-light:#8cc540;
  --green-dark:#3f8a2c;
  --ink:#4a4a4a;
  --text:#555555;
  --paper:#ffffff;
  --bg:#eeeeee;
  --slate:#3e3e3e;
  --slate-light:#6a6a6a;
  --teal:#2fa3b8;
}
*{box-sizing:border-box;margin:0;padding:0}
html,body{width:1200px;height:937px;overflow:hidden}
body{background:var(--bg);font-family:"Arimo",Arial,sans-serif;color:var(--text);position:relative}
.piece{position:absolute;background:var(--paper);overflow:hidden}
.band{position:absolute;left:0;right:0;background:linear-gradient(90deg,var(--green-dark),var(--green-light) 55%,var(--green));border-top:2px solid var(--paper);box-shadow:0 -3px 0 var(--green)}
.band-url{color:#fff;letter-spacing:3px;font-size:9px;line-height:10px;text-align:center;white-space:nowrap}
.band-url b{font-weight:700}
.brand{position:absolute;display:flex;align-items:center;gap:6px;white-space:nowrap}
.brand-mark{border-radius:50%;background:var(--green);flex:none}
.brand-name{font-family:"Montserrat",Arial,sans-serif;font-weight:600;color:var(--ink);line-height:1;white-space:nowrap}
.faint-disc{position:absolute;border-radius:50%;border:14px solid rgba(90,168,58,.07);background:rgba(90,168,58,.04)}

/* letterhead */
.letterhead{left:185px;top:66px;width:388px;height:548px}
.letterhead .brand{left:20px;top:28px}
.letterhead .brand-mark{width:34px;height:34px}
.letterhead .brand-name{font-size:15px}
.sender{position:absolute;right:18px;top:24px;text-align:right;font-size:5px;line-height:7px;font-style:normal}
.letter{position:absolute;left:38px;top:140px;width:300px;font-size:5px;line-height:7.4px}
.letter p{margin-bottom:9px}
.letter .gap{margin-bottom:22px}
.signature{height:18px;width:26px;border-bottom:1px solid var(--ink);margin:2px 0 6px}
.letterhead .faint-disc{left:160px;top:350px;width:210px;height:210px}
.letterhead .band{bottom:0;height:26px;padding-top:7px}

/* cover sheet */
.cover{left:636px;top:40px;width:458px;height:577px}
.cover .brand{left:0;right:0;top:236px;gap:10px;justify-content:center}
.cover .brand-mark{width:90px;height:90px}
.cover .brand-name{font-size:34px}
.cover .band{bottom:0;height:24px;padding-top:6px}

/* business cards */
.card-front{left:45px;top:659px;width:177px;height:99px}
.card-front .brand{left:7px;top:10px;gap:4px}
.card-front .brand-mark{width:22px;height:22px}
.card-front .brand-name{font-size:10px}
.card-contact{position:absolute;left:8px;top:66px;font-size:3.6px;line-height:5px}
.card-holder{position:absolute;right:8px;top:68px;text-align:right;font-size:4px}
.card-holder b{color:var(--teal);font-weight:400;font-size:6px;display:block}
.card-front .band{bottom:0;height:9px;padding-top:0}
.card-front .band-url{font-size:5px;line-height:7px;letter-spacing:1px}
.card-back{left:45px;top:785px;width:177px;height:100px;background:radial-gradient(ellipse at center,var(--slate-light),var(--slate));display:flex;align-items:center;justify-content:center;color:#fff;font-size:6px;letter-spacing:1px}

/* envelope front */
.envelope{left:265px;top:671px;width:432px;height:209px}
.envelope .brand{left:16px;top:28px}
.envelope .brand-mark{width:36px;height:36px}
.envelope .brand-name{font-size:16px}
.envelope .faint-disc{left:270px;top:70px;width:150px;height:150px}
.envelope .band{bottom:0;height:24px;padding-top:6px}

/* envelope back */
.envelope-back{left:736px;top:671px;width:381px;height:209px}
.flap{position:absolute;left:0;right:0;top:0;height:72px;border-radius:0 0 40px 40px;background:linear-gradient(90deg,var(--green-dark),var(--green-light) 50%,var(--green-dark));padding-top:30px}
</style>
</head>
<body>

<section class="piece letterhead" aria-label="Letterhead">
  <div class="brand"><span class="brand-mark"></span><span class="brand-name">4627 Holdings</span></div>
  <address class="sender">220 Harbour Lane<br>Toronto ON M5J 2N8<br><span style="color:var(--teal)">416.555.0142</span><br>dana@4627holdings.com</address>
  <div class="faint-disc"></div>
  <div class="letter">
    <p>July 2, 2012</p>
    <p><b>Dear Cli,</b><br>ABC Building, def St., Country Name</p>
    <p>is simply dummy text of the printing and typesetting industry. Lorem Ipsum has been the industry's standard dummy text ever since the 1500s, when an unknown printer took a galley of type and scrambled it to make a type specimen book. It has survived not only five centuries, but also the leap into electronic typesetting, remaining essentially unchanged. It was popularised in the 1960s with the release of Leafset sheets containing Lorem Ipsum passages, and more recently with desktop publishing software like Pagecraft Studio including versions of Lorem Ipsum.</p>
    <p class="gap">is simply dummy text of the printing and typesetting industry. Lorem Ipsum has been the industry's standard dummy text ever since the 1500s, when an unknown printer took a galley of type and scrambled it to make</p>
    <p>is simply dummy text of the printing and typesetting industry. Lorem Ipsum has been the industry's standard dummy text ever since the 1500s, when an unknown printer took a galley of type and scrambled it to make a type specimen book. It has survived not only five centuries, but also the leap into electronic typesetting, remaining essentially unchanged. It was popularised in the 1960s with the release of Leafset sheets containing Lorem Ipsum passages, and more recently with desktop publishing software like Pagecraft Studio including versions of Lorem Ipsum.</p>
    <p>Best Regards,</p>
    <div class="signature"></div>
    <p><b>Owen Marsh</b><br>Director<br><br>4627 Vantor Holdings Inc.</p>
  </div>
  <div class="band"><p class="band-url">www.<b>Sample</b>.com</p></div>
</section>

<section class="piece cover" aria-label="Presentation cover">
  <div class="brand"><span class="brand-mark"></span><span class="brand-name">4627 Holdings</span></div>
  <div class="band"><p class="band-url">www.<b>Sample</b>.com</p></div>
</section>

<section class="piece card-front" aria-label="Business card front">
  <div class="brand"><span class="brand-mark"></span><span class="brand-name">4627 Holdings</span></div>
  <p class="card-contact">T: 416.555.0142<br>E: dana@4627holdings.com<br>220 Harbour Lane, Toronto ON M5J 2N8</p>
  <p class="card-holder"><b>Dana Whitfield</b>Owner</p>
  <div class="band"><p class="band-url">www.<b>Sample</b>.com</p></div>
</section>

<section class="piece card-back" aria-label="Business card back">www.<b>Sample</b>.com</section>

<section class="piece envelope" aria-label="Envelope front">
  <div class="brand"><span class="brand-mark"></span><span class="brand-name">4627 Holdings</span></div>
  <div class="faint-disc"></div>
  <div class="band"><p class="band-url">www.<b>Sample</b>.com</p></div>
</section>

<section class="piece envelope-back" aria-label="Envelope back">
  <div class="flap"><p class="band-url">www.<b>Sample</b>.com</p></div>
</section>

</body>
</html>
```